Corporate Business Card

Very professional, Modern, Not to busy, include phone address email, website
(253) 617-4930, 18761 52nd Avenue S, Kent, WA 98047, martin@plumlinegroup.com, varkoworks.com

Target Market(s)

Manufacturing

Industry/Entity Type

Aero, machining, manufacturing, Off road racing

Contact Information for Business Card

Phone, address email, website

```html
<!DOCTYPE html>
<html lang="en">
<head>
<meta charset="utf-8">
<title>Varko Works – Business Card</title>
<link rel="stylesheet" href="https://fonts.googleapis.com/css2?family=Montserrat:wght@400;500;700;800&display=swap">
<style>
  :root {
    --navy: #173872;
    --red: #d4222b;
    --white: #ffffff;
    --silver: #c9cbce;
    --ink: #151515;
    --backdrop: #2b2b2d;
  }
  * { box-sizing: border-box; margin: 0; padding: 0; }
  html, body {
    width: 1200px;
    height: 1015px;
    overflow: hidden;
    background: var(--backdrop);
    font-family: "Montserrat", Arial, sans-serif;
  }
  .sheet {
    position: relative;
    width: 1200px;
    height: 1015px;
  }
  .card {
    position: absolute;
    left: 232px;
    width: 735px;
    height: 420px;
    overflow: hidden;
    box-shadow: 0 10px 28px rgba(0,0,0,0.45);
  }
  .card--front {
    top: 58px;
    background: var(--navy);
  }
  .card--back {
    top: 537px;
    background: var(--white);
  }

  /* front */
  .front-name {
    position: absolute;
    left: 0;
    right: 0;
    top: 160px;
    text-align: center;
    font-weight: 800;
    font-size: 78px;
    letter-spacing: 2px;
    color: var(--silver);
    text-transform: uppercase;
    line-height: 1;
  }

  /* back */
  .back-name {
    position: absolute;
    right: 50px;
    top: 52px;
    display: flex;
    align-items: center;
    gap: 12px;
    font-weight: 800;
    font-size: 40px;
    letter-spacing: 1px;
    color: var(--navy);
    text-transform: uppercase;
    line-height: 1;
  }
  .back-name .mark-square {
    width: 16px;
    height: 16px;
    background: var(--red);
  }
  .address {
    position: absolute;
    left: 48px;
    top: 158px;
    font-size: 17px;
    font-weight: 500;
    line-height: 1.35;
    color: var(--ink);
  }
  .contact-list {
    position: absolute;
    left: 48px;
    top: 236px;
    list-style: none;
  }
  .contact-list li {
    display: flex;
    align-items: center;
    gap: 10px;
    font-size: 16px;
    font-weight: 500;
    color: var(--ink);
    height: 27px;
  }
  .contact-list svg {
    width: 17px;
    height: 17px;
    fill: var(--red);
    flex: none;
  }
  .wave {
    position: absolute;
    left: 0;
    top: 0;
    width: 735px;
    height: 420px;
  }
  .wave .band { fill: var(--navy); }
  .wave .stripe { fill: var(--red); }
</style>
</head>
<body>
<main class="sheet">

  <section class="card card--front" aria-label="Card front">
    <p class="front-name">Varko Works</p>
  </section>

  <section class="card card--back" aria-label="Card back">
    <svg class="wave" viewBox="0 0 735 420" aria-hidden="true">
      <path class="stripe" d="M0,336 C240,328 360,292 470,218 C570,152 640,134 712,128 C650,140 585,166 490,232 C380,308 250,350 0,356 Z"/>
      <path class="band" d="M0,370 C250,362 385,326 500,248 C600,182 670,160 735,150 L735,420 L0,420 Z"/>
    </svg>

    <div class="back-name">
      <span class="mark-square"></span>
      <span>Varko Works</span>
    </div>

    <address class="address" style="font-style: normal;">
      18761 52nd Avenue<br>
      S, Kent, WA 98047
    </address>

    <ul class="contact-list">
      <li>
        <svg viewBox="0 0 24 24" aria-hidden="true"><path d="M6.6 10.8a15.1 15.1 0 0 0 6.6 6.6l2.2-2.2a1 1 0 0 1 1-.25 11.4 11.4 0 0 0 3.6.57 1 1 0 0 1 1 1V20a1 1 0 0 1-1 1A17 17 0 0 1 3 4a1 1 0 0 1 1-1h3.5a1 1 0 0 1 1 1c0 1.25.2 2.45.57 3.57a1 1 0 0 1-.25 1z"/></svg>
        (253) 617-4930
      </li>
      <li>
        <svg viewBox="0 0 24 24" aria-hidden="true"><path d="M2 5h20v14H2z M3.5 6.5 12 13l8.5-6.5" stroke="#fff" stroke-width="1.5"/></svg>
        martin@plumlinegroup.com
      </li>
      <li>
        <svg viewBox="0 0 24 24" aria-hidden="true"><circle cx="12" cy="12" r="10"/><path d="M2 12h20M12 2c3 3 3 17 0 20M12 2c-3 3-3 17 0 20" stroke="#fff" stroke-width="1.3" fill="none"/></svg>
        www.varkoworks.com
      </li>
    </ul>
  </section>

</main>
</body>
</html>
```